Brightwell Supports

We need an updated website that captures the comprehensive services and supports we provide to persons with developmental disabilities. We need a website design that educates families about the services we provide. We would also need a website that is user-friendly so that we could periodically update training schedules and ongoing programming.

• Thank you for submitting designs.  A few things I am hoping to see offered in the website:
• Front page highlights the services we offer (host homes, family caregiver, day program, employment program, SLS program, supported apartment program, behavior/clinical program)
• Front page also highlights any new programs we want to make prominent:  family caregiver, future restaurant employment openings, etc...
• Interactive Training Calendar
• Employee Resources page (link to carevo, email login, etc.)
• Uniform provider application for host home providers
• Information on agency - history, goals, etc.
• Contact Information/Location

 

Fun things to include:

• Client Highlights (featuring a client story each month, etc...)
• Employee highlights (featuring a staff member...)
• link to other Brightwell business pages (Brightwell Therapy and Brightwell Restaurant)

```html
<!DOCTYPE html>
<html lang="en">
<head>
<meta charset="utf-8">
<title>Employee Resources – Brightwell Supports</title>
<link href="https://fonts.googleapis.com/css2?family=Raleway:wght@400;500;600;700&family=Open+Sans:wght@400;600;700&display=swap" rel="stylesheet">
<style>
:root{
  --maroon:#7b1c2c;
  --maroon-dark:#611423;
  --grey-bar:#8b8b8e;
  --grey-mid:#8e8e91;
  --grey-dark:#5f5f62;
  --grey-light:#a3a3a6;
  --footer:#848487;
  --black:#0c0c0c;
  --text:#2a2a2a;
  --white:#ffffff;
}
*{margin:0;padding:0;box-sizing:border-box}
html,body{width:1041px;height:1200px;overflow:hidden;background:var(--white)}
body{position:relative;font-family:"Raleway",sans-serif;color:var(--text)}
a{color:inherit;text-decoration:none}

.top-bar{position:absolute;left:0;top:0;width:1041px;height:35px;background:var(--grey-bar);color:var(--white);font-family:"Open Sans",sans-serif;font-size:8px;letter-spacing:.5px}
.social{position:absolute;left:172px;top:12px;display:flex;gap:9px}
.social span{width:12px;height:12px;border-radius:50%;background:#d7d7d9}
.top-contact{position:absolute;right:210px;top:13px;display:flex;gap:22px;align-items:center}
.top-contact .item{display:flex;align-items:center;gap:5px}
.top-contact .sep{width:1px;height:14px;background:#c6c6c8}

.header{position:absolute;left:0;top:35px;width:1041px;height:71px;background:var(--white)}
.brand{position:absolute;left:154px;top:20px;display:flex;align-items:center;gap:8px;font-family:"Raleway",sans-serif;font-weight:700;font-size:17px;color:var(--maroon)}
.brand .dot{width:14px;height:14px;border-radius:50%;background:var(--maroon)}
.nav{position:absolute;left:410px;top:0;height:71px;display:flex}
.nav a{display:flex;align-items:center;justify-content:center;text-align:center;padding:0 14px;font-size:7.5px;font-weight:700;color:var(--maroon);letter-spacing:.4px;line-height:1.2;height:71px;border-right:1px solid #e2e2e2}
.nav a:last-child{border-right:0}
.nav a.active{background:var(--maroon);color:var(--white);height:71px;width:66px;border:0}

.crumbs{position:absolute;left:0;top:106px;width:1041px;height:21px;background:var(--maroon);color:var(--white);font-size:7.5px;font-weight:600;padding:6px 0 0 161px}

.links{position:absolute;left:154px;top:152px;width:152px}
.links h2{height:42px;background:var(--maroon);color:var(--white);font-size:15px;font-weight:700;text-align:center;line-height:42px;letter-spacing:.5px}
.links li{list-style:none;height:22px;line-height:22px;padding-left:10px;font-size:7px;color:var(--white)}
.links li:nth-child(odd){background:var(--grey-dark)}
.links li:nth-child(even){background:var(--grey-light)}
.links li.first{background:var(--grey-light);padding-left:36px;height:20px}

.content{position:absolute;left:347px;top:152px;width:520px}
.content h1{font-size:15px;font-weight:700;color:var(--maroon);margin-top:0}
.quick-links{font-size:9px;color:var(--maroon);margin-top:9px;word-spacing:2px}
.content h3{font-size:14px;font-weight:700;color:var(--text);margin-top:40px}
.closures{list-style:none;margin-top:36px}
.closures li{font-size:15px;height:30.7px;color:var(--text)}
.apply{margin-top:25px;font-size:14px}
.apply-email{display:block;text-align:center;margin-top:15px;font-size:14px;color:var(--maroon)}

.testimonial{position:absolute;left:347px;top:766px;width:512px;height:82px;background:var(--grey-mid);color:var(--white);text-align:right;padding:14px 56px 0 20px}
.testimonial q{display:block;font-size:12.5px;font-style:italic;font-weight:400;line-height:1.3}
.testimonial cite{display:block;font-style:normal;font-size:8px;font-weight:700;margin-top:6px;padding-right:2px}

.footer{position:absolute;left:0;top:1014px;width:1041px;height:167px;background:var(--footer);color:#ededee;font-family:"Open Sans",sans-serif}
.footer .col{position:absolute;top:43px}
.footer h4{font-size:8px;font-weight:700;letter-spacing:.6px;color:var(--white);padding-bottom:5px;border-bottom:1px solid #a9a9ac;width:118px}
.footer p,.footer li{font-size:7px;line-height:14px;list-style:none}
.footer .body{margin-top:18px}
.subscribe input{display:block;width:137px;height:11px;border:0;margin-top:10px;font-size:6px;padding-left:4px;font-family:"Open Sans",sans-serif;color:#888}
.subscribe button{display:block;width:93px;height:10px;margin-top:4px;background:var(--maroon);border:0;color:var(--white);font-size:5px}
.bottom-bar{position:absolute;left:0;top:1181px;width:1041px;height:19px;background:var(--black);color:var(--white);font-size:8px;text-align:center;line-height:19px;letter-spacing:1.6px;font-family:"Open Sans",sans-serif}
</style>
</head>
<body>

<div class="top-bar">
  <div class="social"><span></span><span></span><span></span><span></span><span></span></div>
  <div class="top-contact">
    <div class="item">24/7 SUPPORT
      <svg width="10" height="10" viewBox="0 0 24 24"><path fill="#fff" d="M6.6 10.8a15 15 0 006.6 6.6l2.2-2.2c.3-.3.7-.4 1-.2 1.1.4 2.3.6 3.6.6.6 0 1 .4 1 1V20c0 .6-.4 1-1 1A17 17 0 013 4c0-.6.4-1 1-1h3.5c.6 0 1 .4 1 1 0 1.3.2 2.5.6 3.6.1.3 0 .7-.2 1z"/></svg>
      +1 555 014 2290</div>
    <div class="sep"></div>
    <div class="item">
      <svg width="14" height="10" viewBox="0 0 14 10"><rect x=".5" y=".5" width="13" height="9" fill="none" stroke="#fff"/><path d="M.5.5 7 5.5 13.5.5" fill="none" stroke="#fff"/></svg>
      HELLO@BRIGHTWELLMAIL.ORG</div>
    <div class="sep"></div>
    <div class="item">
      <svg width="10" height="10" viewBox="0 0 10 10"><circle cx="4" cy="4" r="3" fill="none" stroke="#fff" stroke-width="1.5"/><path d="M6.2 6.2 9.5 9.5" stroke="#fff" stroke-width="1.6"/></svg>
      SEARCH</div>
  </div>
</div>

<header class="header">
  <div class="brand"><span class="dot"></span>Brightwell Supports</div>
  <nav class="nav">
    <a href="#">SERVICES</a>
    <a href="#">BECOME A<br>PROVIDER</a>
    <a href="#" class="active">PROGRAMS</a>
    <a href="#">LOCATION</a>
    <a href="#">COMMUNITY<br>RESOURCES</a>
    <a href="#">SUPPORT</a>
    <a href="#">OUR TEAM</a>
  </nav>
</header>

<div class="crumbs">Home &nbsp;»&nbsp; Employee Resources</div>

<aside class="links">
  <h2>LINKS</h2>
  <ul>
    <li class="first">&amp;</li>
    <li>Future Restaurant Employment openings</li>
    <li>Future Restaurant</li>
    <li>Future Restaurant Employment openings</li>
    <li>Future Restaurant</li>
    <li>Future Restaurant Employment openings</li>
    <li>Future Restaurant</li>
    <li>Future Restaurant Employment openings</li>
  </ul>
</aside>

<main class="content">
  <h1>EMPLOYEE RESOURCES</h1>
  <p class="quick-links">Employee Email Login: &nbsp;Login mailportal.net</p>
  <h3>Agency Closure Days - 2013</h3>
  <ul class="closures">
    <li>New Year's Day - Tuesday, January 1st</li>
    <li>President's Day - Monday, February 18th</li>
    <li>Memorial Day - Monday, May 27th</li>
    <li>Independence Day - Thursday, July 4th</li>
    <li>Labor Day - Monday, September 2nd</li>
    <li>Veterans Day - Monday, November 11th</li>
    <li>Thanksgiving - Thursday, November 28nd</li>
    <li>Thanksgiving - Friday, November 29th</li>
    <li>Christmas Eve - Tuesday, December 24th</li>
    <li>Christmas - Wednesday, December 25th</li>
  </ul>
  <p class="apply">If You Are Interested In Employment Options, Please Email Your Resume To</p>
  <a class="apply-email" href="#">maren@brightwellsupports.com</a>
</main>

<blockquote class="testimonial">
  <q>"Praesent vestibulum aenean nonummy hendrerit mauris! Whether you need a motor for a precise medical application."</q>
  <cite>Peter Lindqvist, CEO Norvale Motion</cite>
</blockquote>

<footer class="footer">
  <div class="col" style="left:166px">
    <h4>ABOUT US</h4>
    <div class="body">
      <p>418 Alder Row</p>
      <p>Fairhaven, CO 80999</p>
      <p>Phone: 555-010-4471</p>
      <p>Fax: 555-010-4472</p>
    </div>
  </div>
  <div class="col" style="left:361px">
    <h4>COMPANY</h4>
    <ul class="body"><li>About</li><li>Career</li><li>Media Kit</li><li>Contact Us</li></ul>
  </div>
  <div class="col subscribe" style="left:534px">
    <h4 style="width:146px">SUBSCRIBE TO OUR NEWSLETTER</h4>
    <p class="body" style="width:110px;line-height:9px">Get our latest program updates and event news</p>
    <input type="text" value="Email Address" aria-label="Email address">
    <button type="button">Subscribe</button>
  </div>
  <div class="col" style="left:754px">
    <h4>HELP &amp; SUPPORT</h4>
    <ul class="body"><li>Terms</li><li>Privacy</li><li>Sign Up</li><li>Login</li></ul>
  </div>
</footer>
<div class="bottom-bar">© 2014 ALL RIGHTS RESERVED PRIVACY POLICY</div>

</body>
</html>
```